wealth management firm, professional group, new model

we have a logo that works but we need a card, white background using our colors...clean look

our tag line if can be used in

Your Path From Saving to Growth

```html
<!DOCTYPE html>
<html lang="en">
<head>
<meta charset="utf-8">
<title>Halvern Wealth Partners – Business Card</title>
<link href="https://fonts.googleapis.com/css2?family=Lato:wght@400;700;900&display=swap" rel="stylesheet">
<style>
  :root {
    --navy: #1a2e50;
    --ink: #555a60;
    --stage: #e9e9e9;
    --paper: #ffffff;
    --silver: #a9a9a9;
  }
  * { margin: 0; padding: 0; box-sizing: border-box; }
  html, body { width: 1200px; height: 1000px; overflow: hidden; }
  body {
    background: var(--stage);
    font-family: "Lato", Arial, sans-serif;
    position: relative;
  }
  .card {
    position: absolute;
    left: 254px;
    width: 692px;
    height: 396px;
    border-radius: 22px;
    overflow: hidden;
    box-shadow: 0 3px 8px rgba(0,0,0,0.18);
  }
  .card--front { top: 78px; background: var(--paper); }
  .card--back { top: 526px; background: var(--navy); }

  .brand {
    position: absolute;
    right: 46px;
    top: 96px;
    width: 232px;
    text-align: center;
    color: var(--navy);
    font-weight: 400;
    text-transform: uppercase;
  }
  .brand__name {
    font-size: 38px;
    line-height: 1;
    letter-spacing: 0.3em;
    margin-right: -0.3em;
  }
  .brand__sub {
    font-size: 15px;
    letter-spacing: 0.14em;
    margin-top: 22px;
  }

  .person { position: absolute; left: 39px; top: 166px; }
  .person__name {
    color: var(--navy);
    font-weight: 900;
    font-size: 30px;
    letter-spacing: 0.01em;
    line-height: 1;
  }
  .person__title { color: var(--ink); font-size: 16px; margin-top: 7px; }

  .divider {
    position: absolute;
    left: 39px; right: 46px; top: 236px;
    height: 2px;
    background: var(--navy);
  }

  .contact-list {
    position: absolute;
    left: 39px; top: 255px;
    list-style: none;
    color: var(--ink);
  }
  .contact-list li {
    display: flex; align-items: center;
    height: 24px;
    font-size: 17px;
    letter-spacing: 0.02em;
  }
  .contact-list li.contact--email { font-size: 15px; }
  .contact-list svg { width: 12px; height: 12px; margin-right: 9px; fill: var(--navy); flex: none; }

  .office {
    position: absolute;
    right: 45px; top: 254px;
    text-align: right;
    color: var(--ink);
    font-size: 16px;
    line-height: 24.5px;
    letter-spacing: 0.02em;
  }
  .office__company { color: var(--navy); font-weight: 700; font-size: 15.5px; }

  .footer-band { position: absolute; left: 0; bottom: 0; width: 100%; height: 16px; }

  .back-name {
    position: absolute;
    left: 0; right: 0; top: 152px;
    text-align: center;
    color: var(--paper);
    font-weight: 400;
    font-size: 38px;
    letter-spacing: 0.2em;
    text-transform: uppercase;
  }
  .tagline {
    position: absolute;
    left: 0; right: 0; top: 332px;
    text-align: center;
    color: var(--paper);
    font-size: 17px;
  }
</style>
</head>
<body>

<section class="card card--front">
  <div class="brand">
    <div class="brand__name">Halvern</div>
    <div class="brand__sub">Wealth Partners</div>
  </div>

  <div class="person">
    <div class="person__name">DANIEL CARTER</div>
    <div class="person__title">Founder &amp; CEO</div>
  </div>

  <div class="divider"></div>

  <ul class="contact-list">
    <li>
      <svg viewBox="0 0 12 12" aria-hidden="true"><path d="M2.5 0.8l2 2.2-1 1.3c.7 1.5 1.8 2.6 3.3 3.3l1.3-1 2.2 2-1.2 1.9C5.6 10.3 1.7 6.4 0.6 2z"/></svg>
      (123) 456-7890
    </li>
    <li>
      <svg viewBox="0 0 12 12" aria-hidden="true"><path d="M3 0h6a1 1 0 0 1 1 1v10a1 1 0 0 1-1 1H3a1 1 0 0 1-1-1V1a1 1 0 0 1 1-1zm.5 1.5v7.5h5V1.5zM6 9.8a.7.7 0 1 0 0 1.4.7.7 0 0 0 0-1.4z"/></svg>
      (123) 456-7890
    </li>
    <li>
      <svg viewBox="0 0 12 12" aria-hidden="true"><path d="M3 0h6v3H3zM1 4h10a1 1 0 0 1 1 1v4H9.5v3h-7V9H0V5a1 1 0 0 1 1-1zm3 4v2.5h4V8z"/></svg>
      (123) 456-7890
    </li>
    <li class="contact--email">
      <svg viewBox="0 0 12 12" aria-hidden="true"><path d="M0 2h12v1L6 6.5 0 3zm0 2.3l6 3.5 6-3.5V10H0z"/></svg>
      info@yourwebsitehere.com
    </li>
  </ul>

  <div class="office">
    <div class="office__company">Halvern Wealth Partners</div>
    <div>Street Address Here, City</div>
    <div>State, Country, ZIP 123</div>
    <div>www.yourwebsitehere.com</div>
  </div>

  <svg class="footer-band" viewBox="0 0 692 16" preserveAspectRatio="none" aria-hidden="true">
    <polygon points="0,0 462,0 450,16 0,16" fill="var(--navy)"/>
    <polygon points="469,0 692,0 692,16 456,16" fill="var(--silver)"/>
  </svg>
</section>

<section class="card card--back">
  <div class="back-name">Halvern</div>
  <p class="tagline">Your Path From Saving to Growth</p>
</section>

</body>
</html>
```